Website Design for Employee Moral and Happiness Company

Looking for a clean website design that explains our features in a step by step manner so our visitors know exactly what our site does before logging in.

The site is called "Velrato". See logo design and video for a sample of style and an overview of what we do.

Target Market(s)

Business owners that are looking to retain employees.

Number of Pages Required

1 page

```html
<!DOCTYPE html>
<html lang="en">
<head>
<meta charset="utf-8">
<title>Velrato</title>
<link href="https://fonts.googleapis.com/css2?family=Cormorant+Garamond:wght@600;700&family=Lato:wght@400;700&display=swap" rel="stylesheet">
<style>
:root{
  --orange:#e8582a;
  --orange-soft:#ee6c3c;
  --orange-tint:#f6d2c3;
  --ink:#1b1b1b;
  --body:#3a3a3a;
  --line:#4a4a4a;
  --paper:#ffffff;
  --mist:#f1f2f4;
  --night:#000000;
}
*{margin:0;padding:0;box-sizing:border-box}
html,body{width:1200px;height:4633px;overflow:hidden}
body{position:relative;background:var(--paper);font-family:'Lato',sans-serif;color:var(--body)}
.abs{position:absolute}
.serif{font-family:'Cormorant Garamond',serif}

/* hero */
.hero{left:0;top:0;width:1200px;height:640px;background:linear-gradient(180deg,#3a3d42 0%,#5b5a58 45%,#2d2f33 100%)}
.hero-shade{left:0;top:0;width:1200px;height:640px;background:rgba(0,0,0,.38)}
.logo{font-family:'Cormorant Garamond',serif;font-weight:700;color:#fff;font-size:46px;letter-spacing:1px;line-height:1}
.nav{display:flex;font-size:12.5px;color:#fff;letter-spacing:.3px;text-transform:uppercase}
.nav span{margin-right:36px}
.social{display:flex;gap:11px}
.social i{display:block;width:32px;height:32px;border:2px solid var(--orange);border-radius:50%}
.hero-title{left:0;width:1200px;top:232px;text-align:center;color:#fff;font-size:72px;font-weight:700;line-height:1}
.hero-text{left:150px;width:900px;top:318px;text-align:center;color:#fff;font-size:13.5px;line-height:24px}
.btn{display:flex;align-items:center;justify-content:center;border-radius:30px;font-family:'Cormorant Garamond',serif;font-weight:700;letter-spacing:1px;text-transform:uppercase}
.hero-btn{left:513px;top:385px;width:173px;height:52px;background:var(--orange);color:#fff;font-size:15px}
.dots{left:574px;top:584px;display:flex;gap:4px}
.dots i{width:11px;height:11px;border-radius:50%;background:#fff}
.dots i.on{background:var(--orange)}

/* section headings */
.section-title{left:0;width:1200px;text-align:center;color:var(--ink);font-size:40px;font-weight:700;line-height:1}
.rule{width:56px;height:3px;background:var(--orange);left:572px}

/* features */
.timeline{left:599px;top:770px;width:2px;height:1170px;background:var(--line)}
.feature-photo{width:423px;height:301px}
.feature-copy{width:310px}
.feature-copy h3{font-family:'Cormorant Garamond',serif;color:var(--orange);font-size:23px;font-weight:700;line-height:28px}
.feature-copy p{font-size:11.5px;line-height:27px;margin-top:6px;color:var(--body)}
.left{text-align:right}
.dash{height:0;border-top:2px dashed #888}
.node{width:12px;height:12px;border-radius:50%;background:var(--orange)}

/* about */
.about{left:0;top:1940px;width:1200px;height:742px;background:linear-gradient(120deg,#ec6232 0%,#ef7040 55%,#e85c2c 100%)}
.mascot{left:120px;top:2060px;width:452px;height:333px;border-radius:50%;background:radial-gradient(ellipse at center,#fff 0%,#fbe3d8 55%,rgba(255,255,255,0) 72%)}
.about-title{left:606px;top:2008px;color:#fff;font-size:38px;font-weight:700;line-height:1}
.about-text{left:606px;top:2082px;width:474px;color:#fff;font-size:12px;line-height:24px;text-align:justify}
.about-btn{left:605px;top:2389px;width:180px;height:47px;background:#fff;color:var(--orange);font-size:15px}
.video{left:131px;top:2499px;width:936px;height:527px;background:#fff;padding:9px;box-shadow:0 18px 24px rgba(0,0,0,.18)}
.video-scene{width:100%;height:100%;background:linear-gradient(180deg,#2b8f8a 0%,#d9cfbc 45%,#b9ad98 78%,#2f3e6e 100%)}
.play{left:566px;top:2728px;width:68px;height:68px;border-radius:50%;background:var(--orange);display:flex;align-items:center;justify-content:center}

/* testimonials */
.card{width:304px;height:205px;background:#fff;box-shadow:0 2px 10px rgba(0,0,0,.12);text-align:center;padding-top:26px}
.stars{color:var(--orange);font-size:14px;letter-spacing:3px;line-height:1}
.card h4{font-family:'Cormorant Garamond',serif;font-size:15px;font-weight:700;color:var(--ink);margin-top:12px;letter-spacing:.5px}
.card p{font-size:11.5px;line-height:26px;color:var(--body);margin:6px 16px 0}

/* contact */
.contact{left:0;top:3702px;width:1200px;height:598px;background:var(--mist)}
.contact-art{left:280px;top:3896px;width:286px;height:290px;border-radius:14px;background:radial-gradient(ellipse at center,var(--orange-tint) 0%,#f3e4dd 60%,var(--mist) 100%)}
.field{left:637px;width:318px;height:38px;border:1px solid #bdbdbd;border-radius:19px;background:#fff;font-size:11px;color:#444;padding:12px 0 0 22px}
.field.msg{height:81px;border-radius:12px}
.send{left:637px;top:4166px;width:318px;height:38px;background:var(--orange);color:#fff;font-size:14px}

/* footer */
.footer{left:0;top:4300px;width:1200px;height:333px;background:var(--night)}
.foot-nav{left:347px;top:4456px;font-size:12.5px;color:#fff;text-transform:uppercase;display:flex}
.foot-nav span{margin-right:38px}
.foot-social{left:473px;top:4498px;display:flex;gap:17px}
.foot-social i{display:block;width:50px;height:50px;border-radius:50%;background:var(--orange)}
.copy{left:0;width:1200px;top:4568px;text-align:center;color:#fff;font-size:12.5px}
</style>
</head>
<body>

<header>
  <div class="abs hero" role="img" aria-label="Photo of a smiling team of colleagues standing together in an office"></div>
  <div class="abs hero-shade"></div>
  <div class="abs logo" style="left:130px;top:24px">velrato</div>
  <nav class="abs nav" style="left:344px;top:41px">
    <span>Home</span><span>About</span><span>Our Features</span><span>Reviews</span><span>Blog</span><span>Contact</span>
  </nav>
  <div class="abs social" style="left:908px;top:32px"><i></i><i></i><i></i><i></i></div>
  <h1 class="abs hero-title serif">Welcome to Velrato</h1>
  <p class="abs hero-text">Lorem ipsum dolor sit amet, consectetur adipiscing elit, sed do eiusmod tempor incididunt ut labore et dolore magna aliqua. Ut enim ad minim veniam,<br>quis nostrud exercitation ullamco laboris nisi ut aliquip ex ea commodo consequat.</p>
  <div class="abs btn hero-btn">Get Started</div>
  <div class="abs dots"><i></i><i class="on"></i><i></i><i></i></div>
</header>

<section class="features">
  <h2 class="abs section-title serif" style="top:722px">Our Features</h2>
  <div class="abs rule" style="top:768px"></div>
  <div class="abs timeline"></div>

  <div class="abs feature-photo" style="left:644px;top:811px;background:linear-gradient(135deg,#6f7f93,#c9c3bb 60%,#4b5565)" role="img" aria-label="Photo of colleagues laughing together at a computer"></div>
  <div class="abs feature-copy left" style="left:93px;top:889px">
    <h3>Lorem ipsum dolor sit amet<br>consectetur adipiscing elit.</h3>
    <p>Sed ut perspiciatis unde omnis iste natus error sit vo-<br>luptatem accusantium doloremque laudantium, totam<br>rem aperiam, eaque ipsa quae ab.</p>
  </div>
  <div class="abs dash" style="left:412px;top:952px;width:188px"></div>
  <div class="abs node" style="left:406px;top:947px"></div>

  <div class="abs feature-photo" style="left:131px;top:1173px;background:linear-gradient(135deg,#8a6d55,#d8d2c8 55%,#5f5a55)" role="img" aria-label="Photo of a team gathered around a table with laptops"></div>
  <div class="abs feature-copy" style="left:802px;top:1249px">
    <h3>Lorem ipsum dolor sit amet<br>consectetur adipiscing elit.</h3>
    <p>Sed ut perspiciatis unde omnis iste natus error sit vo-<br>luptatem accusantium doloremque laudantium, totam<br>rem aperiam, eaque ipsa quae ab.</p>
  </div>
  <div class="abs dash" style="left:600px;top:1298px;width:183px"></div>
  <div class="abs node" style="left:777px;top:1293px"></div>

  <div class="abs feature-photo" style="left:644px;top:1533px;background:linear-gradient(135deg,#3d4654,#c7ccd2 55%,#58606b)" role="img" aria-label="Photo of business people joining hands over a desk"></div>
  <div class="abs feature-copy left" style="left:93px;top:1609px">
    <h3>Lorem ipsum dolor sit amet<br>consectetur adipiscing elit.</h3>
    <p>Sed ut perspiciatis unde omnis iste natus error sit vo-<br>luptatem accusantium doloremque laudantium, totam<br>rem aperiam, eaque ipsa quae ab.</p>
  </div>
  <div class="abs dash" style="left:412px;top:1660px;width:188px"></div>
  <div class="abs node" style="left:406px;top:1655px"></div>
</section>

<section>
  <div class="abs about"></div>
  <div class="abs mascot" role="img" aria-label="Brand mascot illustration in white on orange"></div>
  <h2 class="abs about-title serif">About Velrato</h2>
  <p class="abs about-text">Lorem ipsum dolor sit amet, consectetur adipiscing elit, sed do eiusmod tempor incididunt ut labore et dolore magna aliqua. Ut enim ad minim veniam, quis nostrud exercitation ullamco laboris nisi ut aliquip ex ea commodo consequat. Duis aute irure dolor in reprehenderit in voluptate velit esse cillum dolore eu fugiat nulla pariatur. Excepteur sint occaecat cupidatat non proident, sunt in culpa qui officia deserunt mollit anim id est laborum Sed ut perspiciatis unde omnis iste natus error sit voluptatem accusantium doloremque laudantium, totam rem aperiam, eaque ipsa quae ab illo inventore veritatis et quasi architecto beatae vitae dicta sunt explicabo. Nemo enim ipsam voluptatem quia voluptas sit aspernatur aut odit aut fugit, sed quia consequuntur magni dolores eos qui ratione voluptatem sequi nesciunt. Neque porro quisquam est, qui dolorem ipsum quia dolor sit amet, consectetur, adipisci velit, sed quia non numquam eius modi tempora .</p>
  <div class="abs btn about-btn">Learn More</div>
  <div class="abs video"><div class="video-scene" role="img" aria-label="Illustrated video still of relaxed coworkers chatting in armchairs"></div></div>
  <div class="abs play"><svg width="26" height="28" viewBox="0 0 26 28"><path d="M4 2 L24 14 L4 26 Z" fill="#fff"/></svg></div>
</section>

<section>
  <h2 class="abs section-title serif" style="top:3092px">Our Client Testimonials</h2>
  <div class="abs rule" style="top:3144px"></div>

  <div class="abs card" style="left:130px;top:3188px"><div class="stars">★★★★★</div><h4>LOREM IPSUM DOLOR SIT AMET</h4><p>Lorem ipsum dolor sit amet, consectetur adipiscing elit, sed do eiusmod tempor incididunt ut labore et dolore magna aliqua. Quis ipsum suspendisse ultrices gravida.</p></div>
  <div class="abs card" style="left:448px;top:3188px"><div class="stars">★★★★★</div><h4>LOREM IPSUM DOLOR SIT AMET</h4><p>Lorem ipsum dolor sit amet, consectetur adipiscing elit, sed do eiusmod tempor incididunt ut labore et dolore magna aliqua. Quis ipsum suspendisse ultrices gravida.</p></div>
  <div class="abs card" style="left:766px;top:3188px"><div class="stars">★★★★★</div><h4>LOREM IPSUM DOLOR SIT AMET</h4><p>Lorem ipsum dolor sit amet, consectetur adipiscing elit, sed do eiusmod tempor incididunt ut labore et dolore magna aliqua. Quis ipsum suspendisse ultrices gravida.</p></div>
  <div class="abs card" style="left:130px;top:3411px"><div class="stars">★★★★★</div><h4>LOREM IPSUM DOLOR SIT AMET</h4><p>Lorem ipsum dolor sit amet, consectetur adipiscing elit, sed do eiusmod tempor incididunt ut labore et dolore magna aliqua. Quis ipsum suspendisse ultrices gravida.</p></div>
  <div class="abs card" style="left:448px;top:3411px"><div class="stars">★★★★★</div><h4>LOREM IPSUM DOLOR SIT AMET</h4><p>Lorem ipsum dolor sit amet, consectetur adipiscing elit, sed do eiusmod tempor incididunt ut labore et dolore magna aliqua. Quis ipsum suspendisse ultrices gravida.</p></div>
  <div class="abs card" style="left:766px;top:3411px"><div class="stars">★★★★★</div><h4>LOREM IPSUM DOLOR SIT AMET</h4><p>Lorem ipsum dolor sit amet, consectetur adipiscing elit, sed do eiusmod tempor incididunt ut labore et dolore magna aliqua. Quis ipsum suspendisse ultrices gravida.</p></div>
</section>

<section>
  <div class="abs contact"></div>
  <h2 class="abs section-title serif" style="top:3781px">Get In Touch</h2>
  <div class="abs rule" style="top:3833px"></div>
  <div class="abs contact-art" role="img" aria-label="Orange line illustration of an envelope with a letter and a confirmation badge"></div>
  <div class="abs field" style="top:3879px">First Name</div>
  <div class="abs field" style="top:3927px">Last Name</div>
  <div class="abs field" style="top:3976px">Phone</div>
  <div class="abs field" style="top:4024px">Email Address</div>
  <div class="abs field msg" style="top:4071px">Message</div>
  <div class="abs btn send">Send</div>
</section>

<footer>
  <div class="abs footer"></div>
  <div class="abs logo" style="left:0;width:1200px;text-align:center;top:4364px;font-size:56px">velrato</div>
  <nav class="abs foot-nav"><span>Home</span><span>About</span><span>Our Features</span><span>Reviews</span><span>Blog</span><span>Contact</span></nav>
  <div class="abs foot-social"><i></i><i></i><i></i><i></i></div>
  <p class="abs copy">© Copyrights 2022 VELRATO &nbsp;| &nbsp;&nbsp;All rights reserved.</p>
</footer>

</body>
</html>
```